Cedarvale Ridge College

We are looking to update our current webpage at www.cedarvaleridge.ca. We would like to make it modern, fresh and appealing to students. We want to keep our logo the same with the logo colours blended in as the primary colours and focus. We are open to reconfiguring content as well.
Reason: Hi, In the next 3 days we will have narrowed our search to 3 designs and will make a choice before the final deadline...
College

```html
<!DOCTYPE html>
<html lang="en">
<head>
<meta charset="utf-8">
<title>Cedarvale Ridge College</title>
<link href="https://fonts.googleapis.com/css2?family=Titillium+Web:wght@400;600&family=Open+Sans:wght@400;600&family=Lobster&display=swap" rel="stylesheet">
<style>
:root{
  --teal:#005248;
  --teal-dark:#00443c;
  --navy:#0f2b5e;
  --page:#eceeed;
  --text:#555;
  --white:#fff;
  --footer:#004a42;
}
*{margin:0;padding:0;box-sizing:border-box}
html,body{width:733px;height:1200px;overflow:hidden}
body{background:var(--page);font-family:"Open Sans",sans-serif;color:var(--text);position:relative}
.abs{position:absolute}
.top-line{left:0;top:0;width:733px;height:2px;background:var(--teal)}
.account-tab{left:574px;top:0;width:96px;height:21px;background:var(--teal);border-radius:0 0 12px 12px;color:var(--white);font:600 7.5px "Open Sans",sans-serif;display:flex;align-items:center;justify-content:center}
.brand{left:61px;top:18px;display:flex;align-items:center;gap:8px}
.brand-mark{width:34px;height:34px;border-radius:50%;background:var(--teal)}
.brand-name{font:600 17px/1.05 "Titillium Web",sans-serif;color:var(--teal);width:110px}
.main-nav{left:61px;top:71px;width:610px;height:44px;background:var(--teal);display:flex;align-items:center;justify-content:center;gap:20px}
.main-nav a{color:var(--white);font:400 9.2px "Open Sans",sans-serif;text-decoration:none}
.slider{left:61px;top:126px;width:610px;height:312px;background:var(--white);box-shadow:0 1px 4px rgba(0,0,0,.25)}
.slide-photo{left:5px;top:6px;width:601px;height:301px;background:linear-gradient(90deg,#5d7a48 0%,#c9b9a5 30%,#7d9a55 55%,#a8b978 80%,#d9dcc6 100%)}
.slide-caption{left:329px;top:125px;width:220px;height:63px;background:var(--teal);color:var(--white);font:17px "Lobster",sans-serif;display:flex;align-items:center;justify-content:center}
.slide-arrow{top:148px;width:19px;height:19px;border-radius:50%;background:var(--white);box-shadow:0 1px 3px rgba(0,0,0,.35)}
.slide-dots{left:259px;top:292px;width:92px;height:16px;background:var(--white);border-radius:10px 10px 0 0;display:flex;justify-content:center;align-items:center;gap:4px}
.slide-dots i{width:6px;height:6px;border-radius:50%;border:1px solid #6a8bb5}
.slide-dots i.on{background:#111;border-color:#111}
.quick-links{left:61px;top:452px;width:610px;height:130px;background:var(--teal);display:flex}
.quick-link{flex:1;display:flex;flex-direction:column;align-items:center;justify-content:center;gap:12px;color:var(--white);font:600 11.5px "Titillium Web",sans-serif;border-right:1px solid rgba(0,0,0,.08)}
.section-title{font:400 18px "Titillium Web",sans-serif;color:var(--teal)}
.welcome-text{left:60px;top:636px;width:380px;font-size:8.2px;line-height:14.6px;color:#666}
.read-more{font-size:8px;color:#222}
.video{left:454px;top:606px;width:217px;height:135px;background:linear-gradient(90deg,#6f6b62,#b7ad9c 45%,#5b4634 55%,#8b8a86)}
.play{left:90px;top:49px;width:36px;height:36px;border-radius:50%;background:#c8392e}
.news-photo{top:813px;width:196px;height:93px}
.news-meta{top:916px;font-size:7.2px;color:#777}
.news-title{top:930px;font-size:7.8px;color:#222}
.admissions{left:482px;top:773px;width:188px;height:173px;background:linear-gradient(135deg,#b8d8c8,#6f95a3 50%,#4f6e7c 70%,#a9d4dc)}
.admissions h3{font:400 15px "Lobster",sans-serif;color:#0d3563;text-align:center;margin-top:10px}
.admissions ul{list-style:none;margin:10px 0 0 16px}
.admissions li{font-size:8.6px;line-height:17.6px;color:#1b2930}
.admissions li::before{content:"";display:inline-block;width:3px;height:3px;background:var(--teal);margin-right:6px;vertical-align:middle}
.campus-card{top:1002px;width:153px;height:108px;color:var(--white);padding:8px 8px}
.campus-card h4{font:400 12px "Open Sans",sans-serif;margin-bottom:4px}
.campus-card p{font:600 6.8px/11.5px "Open Sans",sans-serif}
.footer{left:0;top:1137px;width:733px;height:63px;background:var(--footer);color:var(--white)}
.footer-links{left:61px;top:18px;font-size:6.6px}
.footer-copy{left:61px;top:32px;font-size:6.4px}
.social{top:26px;display:flex;gap:5px;left:597px}
.social i{width:14px;height:14px;background:#3f7fc0;border-radius:2px}
</style>
</head>
<body>
<div class="abs top-line"></div>
<div class="abs account-tab">My Account | Login</div>

<div class="abs brand"><span class="brand-mark"></span><span class="brand-name">Cedarvale Ridge College</span></div>

<nav class="abs main-nav">
  <a>Home</a><a>About Us</a><a>Contact Us</a><a>Consider Cedarvale</a><a>Current Students</a><a>Alumni</a><a>Supporters</a><a>News + Events</a><a>Cedarvale Park</a>
</nav>

<section class="abs slider">
  <div class="abs slide-photo" role="img" aria-label="Smiling student with laptop sitting outdoors among trees"></div>
  <div class="abs slide-caption">educate, equip, and enrich</div>
  <svg class="abs slide-arrow" style="left:24px" viewBox="0 0 19 19"><path d="M11 5l-4 4.5 4 4.5" fill="none" stroke="#333" stroke-width="2"/></svg>
  <svg class="abs slide-arrow" style="left:573px" viewBox="0 0 19 19"><path d="M8 5l4 4.5-4 4.5" fill="none" stroke="#333" stroke-width="2"/></svg>
  <div class="abs slide-dots"><i class="on"></i><i></i><i></i></div>
</section>

<section class="abs quick-links">
  <div class="quick-link">
    <svg width="30" height="30" viewBox="0 0 30 30"><rect x="4" y="4" width="18" height="23" rx="2" fill="#fff"/><rect x="9" y="2" width="8" height="4" fill="#fff"/><path d="M8 11h10M8 15h10M8 19h7" stroke="#005248" stroke-width="1.6"/><circle cx="23" cy="23" r="6" fill="#fff" stroke="#005248" stroke-width="1.5"/><path d="M20 23l2 2 4-4" stroke="#005248" stroke-width="1.6" fill="none"/></svg>
    Apply Today
  </div>
  <div class="quick-link">
    <svg width="30" height="30" viewBox="0 0 30 30"><path d="M6 27l4-8c-3-3-2-8 2-10l8-5c3-1 6 2 4 5l-5 6c-2 2-5 2-7 1" fill="#fff"/><circle cx="17" cy="11" r="3" fill="#005248"/></svg>
    Donate
  </div>
  <div class="quick-link">
    <svg width="30" height="30" viewBox="0 0 30 30"><path d="M3 10L15 3l12 7z" fill="#fff"/><rect x="3" y="11" width="24" height="2" fill="#fff"/><path d="M6 14v9M11 14v9M16 14v9M21 14v9M25 14v9" stroke="#fff" stroke-width="2.4"/><rect x="3" y="24" width="24" height="3" fill="#fff"/></svg>
    Library
  </div>
  <div class="quick-link">
    <svg width="34" height="30" viewBox="0 0 34 30"><rect x="13" y="3" width="18" height="12" fill="none" stroke="#fff" stroke-width="1.6"/><circle cx="8" cy="8" r="3" fill="#fff"/><path d="M5 12h6l-1 7h-1v8H7v-8H6zM11 13l5-3" fill="#fff" stroke="#fff" stroke-width="1.2"/></svg>
    Text for info
  </div>
</section>

<h2 class="abs section-title" style="left:60px;top:605px">Welcome To &nbsp;Our College</h2>
<div class="abs welcome-text">
  <p>Lorem ipsum dolor sit amet, consectetuer adipiscing elit, sed diam nonummy nibh euismod tincidunt ut laoreet dolore magna aliquam erat volutpat. Lorem ipsum dolor sit amet, consectetuer adipiscing elit, sed diam nonummy nibh euismod tincidunt ut laoreet dolore magna aliquam erat volutpat. Lorem ipsum dolor sit amet, consectetuer adipiscing elit, sed diam nonummy nibh euismod tincidunt ut laoreet dolore magna aliquam erat volutpat.Lorem ipsum dolor sit amet, consectetuer adipiscing elit, sed diam nonummy nibh euismod tincidunt ut laoreet dolore magna aliquam erat volutpat.Lorem ipsum dolor sit amet, consectetuer adipiscing elit, sed diam nonummy nibh euismod</p>
  <p class="read-more">Read more....</p>
</div>
<div class="abs video" role="img" aria-label="Campus hallway with college sign on stone wall">
  <svg class="abs play" viewBox="0 0 36 36"><circle cx="18" cy="18" r="18" fill="#c8392e"/><path d="M14 10l12 8-12 8z" fill="#fff"/></svg>
</div>

<h2 class="abs section-title" style="left:60px;top:776px;font-size:15px">News &amp; Events</h2>
<div class="abs news-photo" style="left:60px;background:linear-gradient(90deg,#6b4a30,#d8c9b5 45%,#8c6c4c 80%,#c7b9a6)" role="img" aria-label="Students performing music with guitar"></div>
<div class="abs news-photo" style="left:267px;background:linear-gradient(90deg,#5a4c46,#2b2a2c 40%,#8a6a9a 65%,#6f7f8a)" role="img" aria-label="Group of students gathered outdoors"></div>
<div class="abs news-meta" style="left:60px">Aug 9, 2013 &nbsp;3 comments</div>
<div class="abs news-meta" style="left:268px">Aug 9, 2013 &nbsp;3 comments</div>
<div class="abs news-title" style="left:60px">Lorem ipsum dolor sit amet</div>
<div class="abs news-title" style="left:268px">Lorem ipsum dolor sit amet</div>

<aside class="abs admissions">
  <h3>Admissions</h3>
  <ul>
    <li>Download the full Catalogue</li>
    <li>Apply Today (Application Package)</li>
    <li>Information Request</li>
    <li>Browse our Programs</li>
    <li>Download Forms</li>
    <li>Admissions Information</li>
    <li>Campus Directory</li>
  </ul>
</aside>

<h2 class="abs section-title" style="left:60px;top:971px;font-size:15px">Our Compaus</h2>
<svg class="abs" style="left:658px;top:981px" width="14" height="10" viewBox="0 0 14 10"><path d="M5 1L1 5l4 4M9 1l4 4-4 4" fill="none" stroke="#222" stroke-width="1.6"/></svg>

<div class="abs campus-card" style="left:60px;background:var(--teal)">
  <h4>Photo Tour</h4>
  <p>Lorem ipsum dolor sit amet, consec-tetuer adipiscing elit, sed diam nonummy nibh euismod tincidunt ut laoreet dolore magna aliquam erat volutpat.<br>Read more..</p>
</div>
<div class="abs campus-card" style="left:212px;background:linear-gradient(180deg,#2f3a3a,#3f5a3c 60%,#2a3a22)" role="img" aria-label="Stone campus entrance sign with flower bed"></div>
<div class="abs campus-card" style="left:365px;background:var(--navy)">
  <h4>Campus Map</h4>
  <p>Lorem ipsum dolor sit amet, consec-tetuer adipiscing elit, sed diam nonummy nibh euismod tincidunt ut laoreet dolore magna aliquam erat volutpat.<br><span style="color:#3f7fc0">Read more..</span></p>
</div>
<div class="abs campus-card" style="left:518px;background:linear-gradient(135deg,#2e3f54,#5b6a78 50%,#2a3b3a)" role="img" aria-label="Aerial campus map with location pins"></div>

<footer class="abs footer">
  <div class="abs footer-links">Home &nbsp;| &nbsp;About Us &nbsp;| &nbsp;Products &nbsp;| &nbsp;Contact Us</div>
  <div class="abs footer-copy">© 2014 Company Name &nbsp;All right reserved &nbsp;Term of Use</div>
  <div class="abs social"><i></i><i style="background:#4aa7d8"></i><i style="background:#2f6fa6"></i><i style="background:#e8872a"></i></div>
</footer>
</body>
</html>
```